Corvane Holdings , new business card design

investment firm with corporate clients . need double sided business card , vertical and horizontal options ,logo must be clear. prefer pantone colors only and sharp design. website also www.corvane.ae

Khalid Bin Tarrafi
Managing Director
Tel. +971 4 387 2940
Mobile +971 50 518 2403
khalid@corvane.ae
Q-Span Plaza, officw 18-B07, Warqa Gardens, Dubai

Contact Information for Business Card

Khalid Bin Tarrafi
Managing Director

Font styles to use
Serif

Colors

Designer to choose colors to be used in the design.

```html
<!DOCTYPE html>
<html lang="en">
<head>
<meta charset="utf-8">
<title>Corvane Holdings – Business Card</title>
<link rel="stylesheet" href="https://fonts.googleapis.com/css2?family=Roboto:wght@300;400&family=Roboto+Condensed:wght@500;700&display=swap">
<style>
  :root {
    --backdrop: #dcdcdc;
    --card-white: #f5f5f4;
    --brand-blue: #456d91;
    --ink-dark: #1c1c1c;
    --ink-body: #444444;
    --rule: #c9c9c9;
    --on-blue: #ffffff;
  }
  * { margin: 0; padding: 0; box-sizing: border-box; }
  html, body {
    width: 1200px; height: 960px; overflow: hidden;
    background: var(--backdrop);
  }
  .stage { position: relative; width: 1200px; height: 960px; }

  .card { position: absolute; width: 600px; height: 342px; }
  .card--front { left: 315px; top: 113px; background: var(--card-white); }
  .card--back  { left: 312px; top: 472px; width: 599px; height: 343px; background: var(--brand-blue); }

  .brand-name {
    position: absolute; left: 0; right: 0;
    text-align: center;
    font-family: "Roboto", sans-serif;
    font-weight: 300;
    font-size: 30px;
    letter-spacing: 0.2em;
    text-indent: 0.2em;
    white-space: nowrap;
  }
  .card--front .brand-name { top: 100px; color: var(--ink-dark); }
  .card--back .brand-name  { top: 162px; color: var(--on-blue); }

  .identity {
    position: absolute; right: 301px; top: 207px;
    text-align: right;
  }
  .identity__name {
    font-family: "Roboto Condensed", sans-serif; font-weight: 700;
    font-size: 20px; line-height: 24px; color: var(--brand-blue);
  }
  .identity__role {
    font-family: "Roboto Condensed", sans-serif; font-weight: 500;
    font-size: 15px; line-height: 19px; color: var(--ink-dark);
    margin-bottom: 3px;
  }
  .identity__address {
    font-family: "Roboto", sans-serif; font-weight: 400;
    font-size: 14px; line-height: 19px; color: var(--ink-body);
    font-style: normal;
  }

  .divider {
    position: absolute; left: 321px; top: 206px;
    width: 1px; height: 86px; background: var(--rule);
  }

  .contact-list {
    position: absolute; left: 342px; top: 211px; list-style: none;
  }
  .contact-list li {
    display: flex; align-items: center; gap: 8px;
    height: 19px;
    font-family: "Roboto", sans-serif; font-size: 14px; color: var(--ink-body);
  }
  .contact-list svg { width: 12px; height: 12px; fill: var(--brand-blue); flex: none; }

  .web-address {
    position: absolute; left: 0; right: 0; top: 290px;
    text-align: center;
    font-family: "Roboto", sans-serif; font-size: 13px;
    letter-spacing: 0.75em; text-indent: 0.75em;
    color: var(--on-blue);
  }
</style>
</head>
<body>
<main class="stage">

  <section class="card card--front" aria-label="Business card front">
    <div class="brand-name">CORVANE HOLDINGS</div>

    <div class="identity">
      <div class="identity__name">KHALID BIN TARRAFI</div>
      <div class="identity__role">MANAGING DIRECTOR</div>
      <address class="identity__address">Q-Span Plaza, officw 18-B07<br>Warqa Gardens, Dubai</address>
    </div>

    <div class="divider"></div>

    <ul class="contact-list">
      <li>
        <svg viewBox="0 0 24 24" aria-hidden="true"><path d="M6.6 10.8a15.1 15.1 0 0 0 6.6 6.6l2.2-2.2c.3-.3.7-.4 1-.2 1.1.4 2.3.6 3.6.6.6 0 1 .4 1 1V20c0 .6-.4 1-1 1A17 17 0 0 1 3 4c0-.6.4-1 1-1h3.5c.6 0 1 .4 1 1 0 1.3.2 2.5.6 3.6.1.3 0 .7-.2 1z"/></svg>
        <span>+971 4 387 2940</span>
      </li>
      <li>
        <svg viewBox="0 0 24 24" aria-hidden="true"><path d="M7 1h10a2 2 0 0 1 2 2v18a2 2 0 0 1-2 2H7a2 2 0 0 1-2-2V3a2 2 0 0 1 2-2zm0 3v14h10V4zm5 15.2a1.2 1.2 0 1 0 0 2.4 1.2 1.2 0 0 0 0-2.4z"/></svg>
        <span>+971 50 518 2403</span>
      </li>
      <li>
        <svg viewBox="0 0 24 24" aria-hidden="true"><path d="M2 5h20v2l-10 6L2 7zm0 4.3 10 6 10-6V19H2z"/></svg>
        <span>khalid@corvane.ae</span>
      </li>
      <li>
        <svg viewBox="0 0 24 24" aria-hidden="true"><path d="M12 2a10 10 0 1 0 0 20 10 10 0 0 0 0-20zm-1 17.9A8 8 0 0 1 4.2 10L9 15v1a2 2 0 0 0 2 2zm6.9-2.5A2 2 0 0 0 16 16h-1v-3a1 1 0 0 0-1-1H8v-2h2a1 1 0 0 0 1-1V7h2a2 2 0 0 0 2-2v-.4a8 8 0 0 1 2.9 12.8z"/></svg>
        <span>www.corvane.ae</span>
      </li>
    </ul>
  </section>

  <section class="card card--back" aria-label="Business card back">
    <div class="brand-name">CORVANE HOLDINGS</div>
    <div class="web-address">www.corvane.ae</div>
  </section>

</main>
</body>
</html>
```